South Florida Real Estate Brokerage Business

The name is LAKE VORISSA REAL ESTATE.
The company is a Real estate realty based in Miami.
Is targeted to Latin American clients.
Must express luxury, and efficiency.
Target clients for properties around 250k to a million +.
Vorissa means Royal in Latin.
Should communicate safety and knowledge of the product and transaction with a tech edge.

The web design needs to be a Social tool, with Friendloop and other media integration of some sort. Needs to have a Show case place, a Search place (MLS listings) with maps and filters.
Needs to reflect luxury but also mixed with a social edge capable of engaging clients or transition them to communicate with the page.
Include the logo from the uploaded files, feel free to change the color or font per webdesign.
This is a Front en design, layout and graphics.
Possible future programming if approved.
I can receive Quotes for the Code part.

Spanish and English speakers living in Latin America and Canada looking for apartments and houses to buy.

Business

• Search area.
Neighbourhood area.
Could be a blog or news area.
Client registration.
Social Plugin
• Social linking to networks.
Log in with friendloop account.
Friendloop Like.

```html
<!DOCTYPE html>
<html lang="en">
<head>
<meta charset="utf-8">
<title>Lake Vorissa Real Estate</title>
<link rel="stylesheet" href="https://fonts.googleapis.com/css2?family=Noto+Serif:ital,wght@0,400;0,700;1,400;1,700&family=Arimo:wght@400;700&display=swap">
<style>
:root{
  --ink:#231f20;
  --band:#2e2c2d;
  --gold:#c9a063;
  --gold-text:#d9a35c;
  --panel:#524631;
  --slate:#3a3939;
  --orange:#f26522;
  --field:#2b2a2a;
  --white:#ffffff;
  --muted:#8f8a7e;
  --footer-note:#6d6a3a;
}
*{box-sizing:border-box;margin:0;padding:0}
html,body{width:725px;height:1200px;overflow:hidden;background:var(--white)}
body{font-family:"Noto Serif",serif;color:var(--white)}
.stage{position:relative;width:785px;height:1300px;transform:scale(0.9236);transform-origin:0 0;background:var(--white)}
.abs{position:absolute}

/* header */
.masthead{left:0;top:0;width:785px;height:92px;background:var(--ink)}
.brand{left:8px;top:22px;display:flex;align-items:center;gap:7px}
.brand-mark{width:12px;height:12px;background:var(--gold)}
.brand-name{color:var(--gold);font-weight:400;font-size:15px;line-height:1.15;letter-spacing:.5px}
.brand-name small{display:block;font-size:10px;letter-spacing:1.5px;text-align:center}
.account{top:46px;display:flex;align-items:center;gap:5px;font-family:"Arimo",sans-serif;font-size:10px;color:var(--gold-text)}
.account svg{width:18px;height:20px}

.nav{left:0;top:96px;width:785px;height:50px;background:var(--gold);display:flex;align-items:center}
.nav-item{position:absolute;top:3px;height:44px;line-height:44px;font-size:11px;font-weight:700;color:var(--ink);transform:translateX(-50%)}
.nav-item.active{left:18px;width:107px;transform:none;text-align:center;background:var(--band);color:var(--white)}
.nav-sep{position:absolute;top:10px;width:1px;height:17px;background:#8a6a3c}

/* main */
.main{left:0;top:178px;width:785px;height:937px;background:var(--ink)}
.slider{left:18px;top:180px;width:504px;height:288px;border:2px solid var(--gold);background:linear-gradient(180deg,#3d4a7a 0%,#6a5f7a 30%,#8a6a3e 55%,#2d5a60 78%,#3a6f78 100%)}
.slider-arrow{top:308px;width:25px;height:25px}

.search{left:550px;top:180px;width:218px;height:288px;background:var(--panel)}
.panel-title{font-size:13px;font-weight:700;color:var(--white)}
.dotted{height:0;border-top:1px dotted var(--gold-text)}
.field-label{font-size:8.5px;color:var(--gold-text)}
.select{height:15px;background:var(--field);border:1px solid #d8d4c8;font-size:7.5px;line-height:13px;padding-left:5px;color:#d6d2c8}
.select::after{content:"";position:absolute;right:0;top:0;width:24px;height:13px;border-left:1px solid #d8d4c8;background:var(--field)}
.select svg{position:absolute;right:7px;top:4px;z-index:1}
.btn-orange{left:593px;top:419px;width:74px;height:15px;background:var(--orange);font-size:8px;text-align:center;line-height:15px;color:var(--white)}
.search-note{left:596px;top:441px;font-size:8px;line-height:12px;color:var(--muted)}
.search-note span{color:var(--gold-text)}

.featured{left:18px;top:468px;width:530px;height:363px;background:var(--panel)}
.section-title{font-size:16px;font-weight:700;color:var(--gold-text)}
.link-small{font-size:9px;font-weight:700;color:var(--gold-text)}
.offer{width:145px}
.offer-title{font-size:8.5px;font-weight:700;text-decoration:underline;line-height:11px}
.offer-sub{font-size:8px;font-weight:700;padding-left:5px;line-height:11px}
.offer-photo{margin-top:17px;width:144px;height:83px;border:1px solid #9a9080}
.offer-meta{margin-top:19px;font-size:8px;font-weight:700;line-height:10px}
.offer-meta span{color:var(--gold-text)}
.offer-text{margin-top:9px;font-size:8.3px;font-weight:700;font-style:italic;line-height:11.3px}
.btn-dark{height:18px;background:var(--field);border:1px solid #cfcac0;font-size:8px;font-weight:700;font-style:italic;text-align:center;line-height:16px;color:var(--white)}
.btn-light{height:17px;background:#d9d7d2;border:1px solid #f0efec;font-size:8px;font-weight:700;font-style:italic;text-align:center;line-height:15px;color:var(--ink)}

.news{left:550px;top:482px;width:218px;height:332px;background:var(--slate)}
.news-heading{left:615px;top:485px;font-size:12px;font-weight:700;text-decoration:underline}
.news-item{left:578px;width:170px}
.date-badge{position:absolute;left:0;top:0;width:24px;height:38px;background:var(--orange);border-radius:2px;font-size:11px;font-weight:700;font-style:italic;text-align:center;line-height:16px;padding-top:3px}
.news-title{position:absolute;left:43px;top:0;font-size:10px;font-weight:700;white-space:nowrap;color:#dedbd4}
.news-title.u{text-decoration:underline}
.news-text{position:absolute;left:40px;top:26px;font-size:7.8px;font-weight:700;font-style:italic;line-height:10.5px;color:#d2cfc8;white-space:nowrap}
.news-rule{left:578px;width:190px;height:1px;background:#222}

.guide{left:18px;top:842px;width:504px;height:253px;background:var(--panel)}
.guide-title{left:41px;top:851px;font-size:13px;font-weight:700}
.guide-sub{left:41px;font-size:10.5px;font-weight:700;color:var(--gold-text)}
.guide-text{left:41px;width:470px;font-size:7.6px;font-weight:700;font-style:italic;line-height:11px}

.story{left:549px;top:842px;width:219px;height:253px;background:var(--slate)}
.story-title{left:560px;top:851px;width:205px;font-family:"Arimo",sans-serif;font-size:9.5px;font-weight:700;line-height:11.5px}
.story-photo{left:560px;top:884px;width:193px;height:65px;border:3px solid #e8e6e2;background:linear-gradient(180deg,#b9c9d6 0%,#8c8a8c 45%,#6e7a56 75%,#4d6b33 100%)}
.story-date{left:563px;top:960px;font-family:"Arimo",sans-serif;font-size:9px;font-weight:700;color:#d6d3cc}
.story-text{left:570px;top:986px;width:190px;font-size:7.8px;font-weight:700;font-style:italic;line-height:11px;color:#d2cfc8}

/* footer */
.band{left:0;top:1115px;width:785px;height:45px;background:var(--band)}
.footer{left:0;top:1160px;width:785px;height:140px;background:var(--ink)}
.foot-head{top:1184px;font-size:8px;font-weight:700}
.foot-rule{left:130px;top:1200px;width:401px;height:0;border-top:1px dotted #d9d6cf}
.foot-links{top:1212px;font-size:8px;font-weight:700;font-style:italic;line-height:11.2px}
.social-head{left:607px;top:1182px;font-size:8px;font-weight:700}
.social{left:622px;display:flex;align-items:center;gap:4px;font-size:7px;color:#d6d3cc}
.social i{display:block;width:14px;height:14px;background:#4a7fb5}
.foot-note{top:1270px;font-family:"Arimo",sans-serif;font-size:10.5px;color:var(--footer-note)}
</style>
</head>
<body>
<div class="stage">

  <header class="abs masthead"></header>
  <div class="abs brand">
    <span class="brand-mark"></span>
    <div class="brand-name">LAKE VORISSA<small>REAL ESTATE</small></div>
  </div>
  <div class="abs account" style="left:619px">
    <svg viewBox="0 0 18 20"><circle cx="9" cy="6" r="5" fill="#e8a04a"/><path d="M1 20c0-6 4-8 8-8s8 2 8 8z" fill="#b8742c"/></svg>Login
  </div>
  <div class="abs account" style="left:686px">
    <svg viewBox="0 0 18 20"><circle cx="9" cy="6" r="5" fill="#f08a3a"/><path d="M1 20c0-6 4-8 8-8s8 2 8 8z" fill="#e06a22"/></svg>Register
  </div>

  <nav class="abs nav">
    <span class="nav-item active">Home</span>
    <span class="nav-item" style="left:172px">Building</span>
    <span class="nav-sep" style="left:229px"></span>
    <span class="nav-item" style="left:279px">Buying</span>
    <span class="nav-sep" style="left:336px"></span>
    <span class="nav-item" style="left:387px">Selling</span>
    <span class="nav-sep" style="left:442px"></span>
    <span class="nav-item" style="left:491px">Moving</span>
    <span class="nav-sep" style="left:548px"></span>
    <span class="nav-item" style="left:602px">Insurance</span>
    <span class="nav-sep" style="left:656px"></span>
    <span class="nav-item" style="left:716px">Contacts</span>
  </nav>

  <main class="abs main"></main>

  <div class="abs slider" role="img" aria-label="Luxury villa with palm trees and a lit pool at dusk"></div>
  <svg class="abs slider-arrow" style="left:8px" viewBox="0 0 25 25"><circle cx="12.5" cy="12.5" r="12" fill="#fff"/><path d="M14.5 8l-5 4.5 5 4.5z" fill="#231f20"/></svg>
  <svg class="abs slider-arrow" style="left:507px" viewBox="0 0 25 25"><circle cx="12.5" cy="12.5" r="12" fill="#fff"/><path d="M10.5 8l5 4.5-5 4.5z" fill="#231f20"/></svg>

  <section class="abs search"></section>
  <h2 class="abs panel-title" style="left:577px;top:187px">Find Your Property</h2>
  <div class="abs dotted" style="left:575px;top:208px;width:137px"></div>
  <div class="abs field-label" style="left:577px;top:223px">City &amp; State, Or Zip:</div>
  <div class="abs select" style="left:576px;top:242px;width:165px"><svg width="10" height="6"><path d="M0 0h10L5 6z" fill="#d8d4c8"/></svg></div>
  <div class="abs field-label" style="left:577px;top:265px">Search Area</div>
  <div class="abs select" style="left:576px;top:280px;width:165px">no radius<svg width="10" height="6"><path d="M0 0h10L5 6z" fill="#d8d4c8"/></svg></div>
  <div class="abs field-label" style="left:577px;top:304px">Price Range</div>
  <div class="abs field-label" style="left:669px;top:304px">to</div>
  <div class="abs select" style="left:576px;top:318px;width:76px">all prices<svg width="8" height="5"><path d="M0 0h8L4 5z" fill="#d8d4c8"/></svg></div>
  <div class="abs select" style="left:666px;top:318px;width:76px">all prices<svg width="8" height="5"><path d="M0 0h8L4 5z" fill="#d8d4c8"/></svg></div>
  <div class="abs field-label" style="left:577px;top:342px">Bedroom(S)</div>
  <div class="abs select" style="left:576px;top:356px;width:165px">any number<svg width="10" height="6"><path d="M0 0h10L5 6z" fill="#d8d4c8"/></svg></div>
  <div class="abs field-label" style="left:579px;top:381px">Bathroom(S)</div>
  <div class="abs select" style="left:576px;top:395px;width:165px">any number<svg width="10" height="6"><path d="M0 0h10L5 6z" fill="#d8d4c8"/></svg></div>
  <div class="abs btn-orange">Proposals</div>
  <p class="abs search-note">Know exactly what you want?<br>Try Our <span>Advanced Search</span></p>

  <section class="abs featured"></section>
  <h2 class="abs section-title" style="left:40px;top:481px">Featured Offers</h2>
  <span class="abs link-small" style="left:475px;top:488px">All offers</span>

  <article class="abs offer" style="left:41px;top:530px">
    <div class="offer-title">SOUTH FLORIDA CONDOS</div>
    <div class="offer-sub">(Condos South of Fifth)</div>
    <div class="offer-photo" role="img" aria-label="Lit condo building facade at night" style="background:linear-gradient(180deg,#2a3a7a 0%,#5a6aa0 45%,#c8c0b0 70%,#3a3f55 100%)"></div>
    <div class="offer-meta">6 BEDS<br>PRICE: <span>$3200000</span></div>
    <p class="offer-text">Pellentesque interdum lobortis feugiat. Phasellus at orci et nisl dapibus molestie. Morbi semper enim a dolor tristique congue. Praesent tellus ante, eleifend in congue</p>
  </article>
  <article class="abs offer" style="left:196px;top:530px">
    <div class="offer-title">SOUTH FLORIDA CONDOS</div>
    <div class="offer-sub">(Aventura Condos)</div>
    <div class="offer-photo" role="img" aria-label="Stone condo entrance with warm window lights" style="background:linear-gradient(180deg,#3a3a2a 0%,#8a7550 45%,#c9a870 70%,#4a4030 100%)"></div>
    <div class="offer-meta">6 BEDS<br>PRICE: <span>$3200000</span></div>
    <p class="offer-text">Pellentesque interdum lobortis feugiat. Phasellus at orci et nisl dapibus molestie. Morbi semper enim a dolor tristique congue. Praesent tellus ante, eleifend in congue</p>
  </article>
  <article class="abs offer" style="left:350px;top:530px">
    <div class="offer-title">SOUTH FLORIDA CONDOS</div>
    <div class="offer-sub">(Bal Harbour Condos)</div>
    <div class="offer-photo" role="img" aria-label="Waterfront resort pavilion at twilight" style="background:linear-gradient(180deg,#2a4aa0 0%,#5a78c0 40%,#a06a3a 65%,#2a4a5a 100%)"></div>
    <div class="offer-meta">6 BEDS<br>PRICE: <span>$3200000</span></div>
    <p class="offer-text">Pellentesque interdum lobortis feugiat. Phasellus at orci et nisl dapibus molestie. Morbi semper enim a dolor tristique congue. Praesent tellus ante, eleifend in congue</p>
  </article>
  <div class="abs btn-dark" style="left:101px;top:795px;width:62px">Details</div>
  <div class="abs btn-dark" style="left:255px;top:795px;width:62px">Details</div>
  <div class="abs btn-dark" style="left:408px;top:795px;width:62px">Details</div>

  <section class="abs news"></section>
  <h2 class="abs news-heading">Latest News</h2>
  <div class="abs dotted" style="left:568px;top:506px;width:175px"></div>
  <div class="abs news-item" style="top:531px">
    <div class="date-badge">20<br>Jan</div>
    <div class="news-title">Hendre maurs phaselus</div>
    <div class="news-text">Varuusm cumsociis natoqe<br>amet penatibus cursusdui...</div>
  </div>
  <div class="abs news-rule" style="top:600px"></div>
  <div class="abs news-item" style="top:620px">
    <div class="date-badge">25<br>Jan</div>
    <div class="news-title u">Hendre maurs phaselus</div>
    <div class="news-text">Varuusm cumsociis natoqe<br>amet penatibus cursusdui...</div>
  </div>
  <div class="abs news-rule" style="top:676px"></div>
  <div class="abs news-item" style="top:699px">
    <div class="date-badge">30<br>Jan</div>
    <div class="news-title u">Hendre maurs phaselus</div>
    <div class="news-text">Varuusm cumsociis natoqe<br>amet penatibus cursusdui...</div>
  </div>
  <div class="abs news-rule" style="top:762px"></div>
  <div class="abs btn-light" style="left:681px;top:777px;width:55px">All News</div>

  <section class="abs guide"></section>
  <h2 class="abs guide-title">Choosing a Real Estate listing Agent</h2>
  <div class="abs dotted" style="left:39px;top:870px;width:480px"></div>
  <h3 class="abs guide-sub" style="top:882px">Market Conditions</h3>
  <p class="abs guide-text" style="top:903px">Sed ut perspiciatis unde omnis iste natus error sit voluptatem accusantium doloremque laudantium, totam rem aperiam, eaque ipsa quae ab illo inventore veritatis et quasi architecto beatae vitae dicta sunt explicabo. Nemo enim ipsam voluptatem quia voluptas sit aspernatur aut odit aut fugit, sed quia consequuntur magni dolores eos ratione</p>
  <h3 class="abs guide-sub" style="top:943px">Finance Calculator</h3>
  <p class="abs guide-text" style="top:964px">Sed ut perspiciatis unde omnis iste natus error sit voluptatem accusantium doloremque laudantium, totam rem aperiam, eaque ipsa quae ab illo inventore veritatis et quasi architecto beatae vitae dicta sunt explicabo. Nemo enim ipsam voluptatem quia voluptas sit aspernatur aut odit aut fugit, sed quia consequuntur magni dolores eos ratione.</p>
  <h3 class="abs guide-sub" style="top:1004px">Home Values</h3>
  <p class="abs guide-text" style="top:1025px">Sed ut perspiciatis unde omnis iste natus error sit voluptatem accusantium doloremque laudantium, totam rem aperiam, eaque ipsa quae ab illo inventore veritatis et quasi architecto beatae vitae dicta sunt explicabo. Nemo enim ipsam voluptatem quia voluptas sit aspernatur aut odit aut fugit, sed quia consequuntur magni dolores eos ratione.</p>
  <div class="abs btn-dark" style="left:293px;top:1070px;width:112px">Click Here To Learn More</div>

  <section class="abs story"></section>
  <h2 class="abs story-title">Sed ut perspiciati natus error sit volunptatem accosoloremque</h2>
  <div class="abs story-photo" role="img" aria-label="Brick suburban house with green lawn"></div>
  <div class="abs story-date">Jan 15,2012</div>
  <p class="abs story-text">Varuusm cumsociis natoqe<br>&nbsp;amet penatibus cursusduiNemo enim ipsam voluptatem quia voluptas sit aspernatur aut odit aut fugit, sed quia consequuntur magni dolores eos ratione.</p>
  <div class="abs btn-light" style="left:640px;top:1069px;width:61px">Read More</div>

  <div class="abs band"></div>
  <footer class="abs footer"></footer>
  <h4 class="abs foot-head" style="left:144px">Company</h4>
  <h4 class="abs foot-head" style="left:242px">PROPERTIES</h4>
  <h4 class="abs foot-head" style="left:352px">FAQS</h4>
  <h4 class="abs foot-head" style="left:439px">FOR CLIENTS</h4>
  <div class="abs foot-rule"></div>
  <div class="abs foot-links" style="left:144px">About US<br>Services<br>Presentation<br>Clients</div>
  <div class="abs foot-links" style="left:242px">Commercial<br>Residental<br>Luxury</div>
  <div class="abs foot-links" style="left:352px">FAQS<br>Support</div>
  <div class="abs foot-links" style="left:439px;top:1209px">Signup<br>Forms<br>Promotions</div>
  <h4 class="abs social-head">Links To Us</h4>
  <div class="abs social" style="top:1202px"><i></i>Chirpnet</div>
  <div class="abs social" style="top:1222px"><i></i>Tumblefind</div>
  <div class="abs social" style="top:1242px"><i></i>Friendloop</div>
  <div class="abs social" style="top:1262px"><i></i>Searchly</div>
  <span class="abs foot-note" style="left:267px">Real Estate @2012</span>
  <span class="abs foot-note" style="left:384px">Privacy Policy</span>

</div>
</body>
</html>
```